Modern Business Card

Modern professional business card with more than just logo and demographic info. Something memorable.

We are a trendy/modern chiropractic group with an emphasis on neurology, hence the minimalist-type brain logo. We want to convey that modern and technical aspect with professionalism and the elite nature of our practice environment.

```html
<!DOCTYPE html>
<html lang="en">
<head>
<meta charset="utf-8">
<title>Meridian Spine – Business Card</title>
<link rel="stylesheet" href="https://fonts.googleapis.com/css2?family=Lato:wght@400;700&display=swap">
<style>
  :root {
    --page: #f1f1f1;
    --card: #fcfcfc;
    --brand-blue: #4a80c6;
    --ink: #141414;
    --muted: #6f6f6f;
    --rule-dark: #111111;
  }
  * { box-sizing: border-box; margin: 0; padding: 0; }
  html, body { width: 1200px; height: 1200px; overflow: hidden; }
  body {
    background: var(--page);
    font-family: "Lato", Arial, sans-serif;
    position: relative;
  }
  .card {
    position: absolute;
    background: var(--card);
    box-shadow: 0 0 0 1px #e4e4e4;
  }
  .card--front { left: 232px; top: 173px; width: 705px; height: 407px; }
  .card--back  { left: 231px; top: 628px; width: 703px; height: 400px; }

  .brand { position: absolute; display: flex; align-items: center; }
  .brand__dot { border-radius: 50%; background: var(--brand-blue); flex: none; }
  .brand__name {
    color: var(--ink);
    font-weight: 700;
    letter-spacing: 0.04em;
    line-height: 1;
    white-space: nowrap;
  }
  .card--front .brand { left: 43px; top: 56px; }
  .card--front .brand__dot { width: 60px; height: 60px; margin-right: 20px; }
  .card--front .brand__name { font-size: 34px; }

  .card--back .brand { left: 50%; top: 50%; transform: translate(-50%, -50%); }
  .card--back .brand__dot { width: 118px; height: 118px; margin-right: 30px; }
  .card--back .brand__name { font-size: 58px; }

  .holder { position: absolute; right: 40px; top: 164px; text-align: right; }
  .holder__name { color: var(--brand-blue); font-size: 31px; line-height: 1.1; }
  .holder__role { color: var(--muted); font-size: 21px; margin-top: 2px; }

  .divider { position: absolute; left: 42px; right: 40px; top: 236px; height: 3px; display: flex; }
  .divider__dark { width: 314px; background: var(--rule-dark); }
  .divider__accent { flex: 1; background: var(--brand-blue); }

  .contacts { position: absolute; left: 42px; top: 258px; list-style: none; }
  .contacts li {
    display: flex; align-items: center;
    height: 27.5px;
    color: var(--muted); font-size: 19px;
  }
  .contacts svg { width: 20px; height: 20px; margin-right: 9px; flex: none; fill: var(--brand-blue); }

  .address { position: absolute; right: 41px; top: 287px; text-align: right; color: var(--muted); font-size: 19px; line-height: 24px; }
  .address__pin { width: 20px; height: 26px; fill: var(--brand-blue); display: block; margin: 0 0 6px auto; }
</style>
</head>
<body>

<section class="card card--front" aria-label="Business card front">
  <div class="brand">
    <span class="brand__dot"></span>
    <span class="brand__name">MERIDIAN SPINE</span>
  </div>

  <div class="holder">
    <p class="holder__name">Calder Voss</p>
    <p class="holder__role">President</p>
  </div>

  <div class="divider"><span class="divider__dark"></span><span class="divider__accent"></span></div>

  <ul class="contacts">
    <li>
      <svg viewBox="0 0 20 20" aria-hidden="true"><path d="M5 1h10a1.5 1.5 0 0 1 1.5 1.5v15A1.5 1.5 0 0 1 15 19H5a1.5 1.5 0 0 1-1.5-1.5v-15A1.5 1.5 0 0 1 5 1zm.5 2.5v11.5h9V3.5zM10 16a1 1 0 1 0 0 2 1 1 0 0 0 0-2z" fill-rule="evenodd"/></svg>
      014 2287 5530
    </li>
    <li>
      <svg viewBox="0 0 20 20" aria-hidden="true"><path d="M2 7c0-2 3.5-3.5 8-3.5S18 5 18 7v1.5h-3.5V7h-9v1.5H2zM5 9.5h10l2 7.5H3zm5 1.5a2.5 2.5 0 1 0 0 5 2.5 2.5 0 0 0 0-5z" fill-rule="evenodd"/></svg>
      014 2287 5530
    </li>
    <li>
      <svg viewBox="0 0 20 20" aria-hidden="true"><path d="M1 4h18v7.5a5 5 0 0 0-7.5 4.5H1zm1.5 1.3 7.5 5.5 7.5-5.5z" fill-rule="evenodd"/><circle cx="16" cy="15.5" r="3.5"/><path d="m14.4 15.5 1.2 1.2 2-2" stroke="#fff" stroke-width="1.2" fill="none"/></svg>
      info@meridianspine.com
    </li>
    <li>
      <svg viewBox="0 0 20 20" aria-hidden="true"><path d="M10 1.5a8.5 8.5 0 1 1 0 17 8.5 8.5 0 0 1 0-17zm0 1.5c-1.3 0-2.6 2.6-2.9 6.2h5.8C12.6 5.6 11.3 3 10 3zm-4.3 6.2c.1-2.3.7-4.3 1.5-5.5A7 7 0 0 0 3 9.2zm8.6 0H17a7 7 0 0 0-4.2-5.5c.8 1.2 1.4 3.2 1.5 5.5zM3 10.8a7 7 0 0 0 4.2 5.5c-.8-1.2-1.4-3.2-1.5-5.5zm4.1 0c.3 3.6 1.6 6.2 2.9 6.2s2.6-2.6 2.9-6.2zm7.2 0c-.1 2.3-.7 4.3-1.5 5.5a7 7 0 0 0 4.2-5.5z" fill-rule="evenodd"/></svg>
      www.meridianspine.com
    </li>
  </ul>

  <div class="address">
    <svg class="address__pin" viewBox="0 0 20 26" aria-hidden="true"><path d="M10 0a9 9 0 0 1 9 9c0 6-9 17-9 17S1 15 1 9a9 9 0 0 1 9-9zm0 5.5a3.5 3.5 0 1 0 0 7 3.5 3.5 0 0 0 0-7z" fill-rule="evenodd"/></svg>
    <p>48 Harlow Street, Suite 200</p>
    <p>Bellmont, NY 10452</p>
  </div>
</section>

<section class="card card--back" aria-label="Business card back">
  <div class="brand">
    <span class="brand__dot"></span>
    <span class="brand__name">MERIDIAN SPINE</span>
  </div>
</section>

</body>
</html>
```